Thoroughbred Racing Partnership needs web design

Glimmer of Laurel Partners is a management group who buys horses and races them on both the West and East coasts. The premise of the business is for an investment as little as $500, anyone can be a partner and own a percentage of a horse(s). This is a low cost way of getting involved in the exciting sport of Thoroughbred Racing, without shouldering the heavy financial responsibility. Our target market is mostly males 40+ but we want to include all target markets. We are looking for something very clean and professional, we want to give an image of success. Nothing overly "artsy." I have included the logo in which you can incorporate in the site. Also, the logo colors will be the colors of our "silks." The silks are what the jockey wears and will be an important marketing tool for GOL. We would like a very prominent picture of a racehorse somewhere on the homepage, we want to make it clear that is a website for Horseracing partnerships.

On the top of the site, it should say "Glimmer of Laurel" (on the top)
and below that "Thoroughbred Racing Partnerships." (below that)

The main sections, which should be across the top are:

Home
About Us
Ownership
Stable Roster
News
Contact us

Some of these will have drop down menus.

An example of a competitor website that we like is: www.harrowgatefarm.example
An example of a competitor website that we don't like is: www.paddockvue.example
Updates

Project Deadline Extended
Reason: We have a Board of Directors meeting on the 22nd and we will be making a decision on that day. I'm giving an extension so that all designers are able to submit their designs by the 22nd. Thank you!

Target Market(s)

40+ males

Industry/Entity Type

Business

Requirements
Must have
• our logo must be on the site. We would like at least one bold image of a thoroughbred horse in action. The picture is going to tell the story so it needs to be very eye-catching.

Our slogan should also be included on the website, "Experience the thrill of owning a Racehorse."
Should not have
• cartoons, artsy pictures, pictures of Steeplechase horses or "jumpers." This partnership is for racehorses only, there is not jumping involved with the horses.

```html
<!DOCTYPE html>
<html lang="en">
<head>
<meta charset="utf-8">
<title>Glimmer of Laurel Partners – Thoroughbred Racing Partnerships</title>
<link rel="stylesheet" href="https://fonts.googleapis.com/css2?family=Roboto:wght@400;500;700&family=Roboto+Slab:wght@400;700&family=Kaushan+Script&display=swap">
<style>
:root{
  --navy:#123a6b;
  --blue:#1f5a9a;
  --sky:#2a86c6;
  --ink:#000;
  --panel:#050505;
  --text-light:#d8d8d8;
  --white:#fff;
  --field:#e6e6e6;
  --grass:#4d6b3a;
}
*{box-sizing:border-box;margin:0;padding:0}
html,body{width:1200px;height:1009px;overflow:hidden;background:#000}
body{position:relative;font-family:"Roboto",sans-serif;color:var(--white)}
.backdrop{position:absolute;inset:0;background:linear-gradient(180deg,#8f9aa0 0%,#6f8a63 18%,var(--grass) 45%,#2e3f2c 100%)}
.topbar{position:absolute;left:147px;top:0;width:906px;height:36px;background:var(--ink);display:flex;align-items:center;justify-content:flex-end;gap:18px;padding-right:20px;font-size:14px}
.topbar a{color:var(--white);text-decoration:none;display:flex;align-items:center;gap:6px}
.topbar .phone{font-weight:700;font-size:18px;margin-left:6px}
.header{position:absolute;left:122px;top:36px;width:956px;height:110px;background:linear-gradient(#fff,#e4e4e4)}
.brand{position:absolute;left:36px;top:26px;display:flex;align-items:center;gap:10px;font-family:"Roboto Slab",serif;font-weight:700;color:var(--navy);font-size:30px;line-height:1}
.brand-mark{width:26px;height:26px;border-radius:50%;background:var(--navy)}
.tagline{position:absolute;right:46px;top:18px;text-align:right;font-family:"Roboto Slab",serif;color:var(--navy);font-size:15.5px;line-height:20px}
.nav{position:absolute;right:42px;top:72px;display:flex;gap:11px;font-family:"Roboto Slab",serif;font-size:16px}
.nav a{color:#777;text-decoration:none}
.nav a.active{color:var(--navy);text-decoration:underline}
.fold{position:absolute;top:146px;width:0;height:0;border-top:24px solid #111}
.fold.l{left:122px;border-left:25px solid transparent}
.fold.r{left:1053px;border-right:25px solid transparent}
.hero{position:absolute;left:147px;top:146px;width:906px;height:495px;background:radial-gradient(ellipse at 35% 55%,#5b3a26 0%,#7a6a5c 32%,#a9a59e 60%,#cfcfcd 100%);overflow:hidden}
.slogan{position:absolute;right:22px;top:44px;width:460px;text-align:center;font-family:"Kaushan Script",cursive;font-size:44px;line-height:52px;color:var(--white);text-shadow:2px 3px 4px rgba(0,0,0,.6)}
.video{position:absolute;left:545px;top:216px;width:374px;height:231px;border:1px solid #222}
.video-frame{position:absolute;inset:0 0 34px 0;background:linear-gradient(135deg,#3a2a1e,#a4561f 50%,#5a3b24)}
.video-play{position:absolute;left:169px;top:91px;width:34px;height:34px;border-radius:50%;background:rgba(0,0,0,.55);border:1px solid #999}
.video-bar{position:absolute;left:0;right:0;bottom:0;height:34px;background:#1b1b1b}
.video-progress{position:absolute;left:0;right:0;top:0;height:4px;background:#c22}
.loginbar{position:absolute;left:122px;top:641px;width:956px;height:47px;background:linear-gradient(#1e4f8c,#0f2f5c);display:flex;align-items:center;padding-left:36px;gap:8px}
.loginbar h2{font-weight:400;font-size:18px;margin-right:10px}
.field{height:26px;border:1px solid #3b6aa5;background:#0b2748;border-radius:3px;color:#fff;font-size:14px;display:flex;align-items:center;justify-content:center}
.f-user,.f-pass{width:168px}
.f-btn{width:108px}
.newto{position:absolute;left:652px;top:4px;display:flex;align-items:center;gap:9px;font-size:14.5px;line-height:18px}
.newto .dot{width:39px;height:39px;border-radius:50%;background:#8b9aa6;border:2px solid #dfe6ee}
.content{position:absolute;left:147px;top:688px;width:906px;height:236px;background:var(--panel)}
.col{position:absolute;top:26px}
.col h3{font-family:"Roboto Slab",serif;font-size:17px;font-weight:700;color:var(--white);text-transform:uppercase;letter-spacing:.3px;margin-bottom:14px}
.col h3 span{color:var(--sky);font-weight:400}
.welcome{left:11px;width:300px}
.welcome p{font-size:14px;line-height:19px;color:var(--text-light);letter-spacing:.4px}
.news{left:366px;width:270px}
.news h4{font-size:13px;font-weight:700;margin-top:2px}
.news p{font-size:13px;line-height:17px;color:var(--text-light);margin-bottom:12px}
.news .more{font-size:14px;color:var(--text-light)}
.member{left:677px;width:220px}
.member .free{font-size:13.5px;font-weight:500;margin:-3px 0 5px}
.member .input{width:175px;height:21px;background:linear-gradient(#fff,#d9d9d9);border:1px solid #888;color:#444;font-size:12px;padding:2px 7px;margin-bottom:5px}
.member .input.tall{height:43px}
.submit{display:inline-block;margin-top:6px;background:var(--blue);border-top:2px solid #2d74bf;padding:1px 10px;font-weight:700;font-size:14px}
.divider{position:absolute;top:14px;width:8px;height:210px;background:linear-gradient(90deg,#000,#1c1c1c,#000)}
.footer{position:absolute;left:0;top:924px;width:1200px;height:85px;background:repeating-linear-gradient(135deg,#1d4f87 0 3px,#214f84 3px 6px)}
.foot-nav{position:absolute;left:158px;top:16px;display:flex;font-size:13px}
.foot-nav a{color:#fff;text-decoration:none;padding:0 7px;border-left:1px solid #8aa9cc}
.foot-nav a:first-child{padding-left:0;border-left:0}
.copy{position:absolute;left:158px;top:38px;font-size:13px;line-height:17px}
.follow{position:absolute;left:680px;top:16px;width:112px;text-align:center;font-size:12px;font-weight:700}
.social{display:flex;justify-content:center;gap:5px;margin-top:9px}
.social span{width:29px;height:29px;border-radius:50%;background:#2b7bc4;border:2px solid #dfe6ee}
.foot-brand{position:absolute;left:920px;top:22px;font-family:"Roboto Slab",serif;font-weight:700;font-size:22px;line-height:24px;color:#fff;text-align:center}
</style>
</head>
<body>
<div class="backdrop" role="img" aria-label="Faded racetrack photograph with horses and jockeys galloping on green turf"></div>

<div class="topbar">
  <a href="#"><svg width="12" height="15" viewBox="0 0 12 15"><rect x="0" y="6" width="12" height="9" rx="1" fill="#fff"/><path d="M3 6V4a3 3 0 0 1 6 0v2" stroke="#fff" stroke-width="2" fill="none"/></svg>Login</a>
  <a href="#"><svg width="18" height="14" viewBox="0 0 18 14"><path d="M1 4v9h13V9" stroke="#fff" stroke-width="2" fill="none"/><path d="M6 9c1-4 4-5 8-5V1l4 4-4 4V6c-3 0-6 1-8 3z" fill="#fff"/></svg>Share This Page</a>
  <span class="phone">Contact Us Now 012-555-0147</span>
</div>

<header class="header">
  <div class="brand"><span class="brand-mark"></span>GOLPARTNERS.COM</div>
  <div class="tagline">GLIMMER OF LAUREL<br>THOROUGHBRED RACING PARTNERSHIPS</div>
  <nav class="nav">
    <a href="#" class="active">Home</a><a href="#">About Us</a><a href="#">Ownership</a><a href="#">Stable Roster</a><a href="#">News</a><a href="#">Contact Us</a>
  </nav>
</header>
<div class="fold l"></div><div class="fold r"></div>

<section class="hero" role="img" aria-label="Large photograph of a jockey in red and white silks riding a bay thoroughbred at full gallop">
  <h1 class="slogan">Experience the thrill of owning a Racehorse</h1>
  <div class="video">
    <div class="video-frame" role="img" aria-label="Video still of two thoroughbreds racing neck and neck"></div>
    <div class="video-play"><svg width="34" height="34" viewBox="0 0 34 34"><path d="M14 11l9 6-9 6z" fill="#fff"/></svg></div>
    <div class="video-bar">
      <div class="video-progress"></div>
      <svg width="374" height="34" viewBox="0 0 374 34"><path d="M22 13l12 7-12 7z" fill="#ccc"/><path d="M62 17h4l5-4v14l-5-4h-4z" fill="#ccc"/><text x="94" y="25" fill="#ccc" font-size="11" font-family="Roboto,sans-serif">0:00</text><rect x="348" y="13" width="12" height="12" fill="none" stroke="#ccc" stroke-width="2" stroke-dasharray="4 4"/></svg>
    </div>
  </div>
</section>

<section class="loginbar">
  <h2>User Login</h2>
  <div class="field f-user">User Name</div>
  <div class="field f-pass">Password</div>
  <div class="field f-btn">Login &gt;</div>
  <div class="newto"><span class="dot" role="img" aria-label="Small photo of a racehorse"></span><span>New to Ownership?<br>Learn About Racing Partnerships</span></div>
</section>

<main class="content">
  <div class="col welcome">
    <h3><span>Welcome to</span> GOL Partners</h3>
    <p>Glimmer of Laurel Partners is a management group who buys horses and races them on both the West and East coasts. The premise of the business is for an investment as little as $500, anyone can be a partner and own a percentage of a horse(s). This is a low cost way of getting involved in the exciting sport of Thoroughbred Racing, without shouldering the heavy financial responsibility.</p>
  </div>
  <div class="divider" style="left:352px"></div>
  <div class="col news">
    <h3><span>Latest</span> News</h3>
    <h4>October 28, 2013</h4>
    <p>Lorem ipsum dolor sit amet, amietconsecte Lorem adipiscing elit,</p>
    <h4>October 26, 2013</h4>
    <p>Lorem ipsum dolor sit amet, amietconsecte Lorem adipiscing elit,</p>
    <div class="more">View All &nbsp;&raquo;</div>
  </div>
  <div class="divider" style="left:677px"></div>
  <div class="col member" style="left:712px">
    <h3><span>Become a</span> GOL Member</h3>
    <div class="free">It's free to join.</div>
    <div class="input">Name*</div>
    <div class="input">Email*</div>
    <div class="input tall">Message*</div>
    <div class="submit">Submit</div>
  </div>
</main>

<footer class="footer">
  <nav class="foot-nav"><a href="#">Home</a><a href="#">About Us</a><a href="#">Ownership</a><a href="#">Stable Roster</a><a href="#">News</a><a href="#">Contact Us</a></nav>
  <div class="copy">Copyright © 2013 - GolPartners<br>All Rights Reserved</div>
  <div class="follow">FOLLOW US ON<div class="social"><span></span><span></span><span></span></div></div>
  <div class="foot-brand">GOL<br>PARTNERS.COM</div>
</footer>
</body>
</html>
```